Using attached logo that has been created

Business card with logo that's attached. Maybe with water or the cartoon van in background. Looking for it to not be so plain and not too white.
Information to include;
Rodney Ashcombe
(555) 218-7730
Info@bramleypipeworks.example
www.bramleypipeworks.example
License # 4627195
Looking forward to the designs u come up with.
Thank you!
-Delphine
Target Market(s)
Plumbing
Industry/Entity Type
Plumbing
Contact Information for Business Card
Listed above

```html
<!DOCTYPE html>
<html lang="en">
<head>
<meta charset="utf-8">
<title>Bramley Pipeworks – Business Card</title>
<link rel="stylesheet" href="https://fonts.googleapis.com/css2?family=Krona+One&family=Arimo:wght@400;700&display=swap">
<style>
  :root {
    --page-bg: #c9c9c9;
    --card-white: #ffffff;
    --brand-blue: #0f56ad;
    --brand-yellow: #fbbf12;
    --water-light: #6cc4e4;
    --water-mid: #2f9ccc;
    --water-deep: #1a6fa3;
    --figure-skin: #c98b62;
    --figure-shirt: #2567c4;
    --van-white: #eef2f5;
  }
  * { margin: 0; padding: 0; box-sizing: border-box; }
  html, body { width: 1200px; height: 800px; overflow: hidden; }
  body {
    background: var(--page-bg);
    display: flex;
    align-items: center;
    justify-content: center;
    gap: 40px;
    font-family: "Arimo", Arial, sans-serif;
  }
  .card {
    position: relative;
    width: 540px;
    height: 310px;
    border-radius: 18px;
    overflow: hidden;
    box-shadow: 0 10px 28px rgba(0,0,0,0.22);
  }

  /* Front */
  .card-front { background: var(--card-white); }
  .holder-name {
    position: absolute;
    left: 34px; top: 66px;
    font-family: "Krona One", sans-serif;
    font-size: 21px;
    letter-spacing: 1px;
    color: var(--brand-blue);
    text-transform: uppercase;
  }
  .contact-band {
    position: absolute;
    left: 0; top: 118px;
    width: 330px; height: 92px;
    background: var(--brand-blue);
    padding: 13px 0 0 34px;
    color: var(--card-white);
    font-size: 15px;
    line-height: 22px;
  }
  .contact-row { display: flex; align-items: center; gap: 8px; }
  .contact-row svg { width: 14px; height: 14px; flex: none; }
  .license {
    position: absolute;
    left: 34px; top: 238px;
    font-size: 17px;
    color: var(--brand-blue);
  }
  .license-number { color: var(--brand-yellow); }
  .accent-square {
    position: absolute;
    right: 70px; top: 0;
    width: 72px; height: 60px;
    background: var(--brand-yellow);
  }
  .mascot-art {
    position: absolute;
    border-radius: 40px 40px 12px 12px;
    background: linear-gradient(180deg, var(--figure-skin) 0%, var(--figure-shirt) 38%, #a08560 100%);
    opacity: 0.85;
  }
  .card-front .mascot-art { left: 370px; top: 40px; width: 120px; height: 190px; }
  .brand-name {
    position: absolute;
    font-family: "Krona One", sans-serif;
    color: var(--brand-blue);
    text-align: center;
    line-height: 1.15;
  }
  .card-front .brand-name { left: 330px; top: 222px; width: 200px; font-size: 17px; }

  /* Back */
  .card-back {
    background:
      radial-gradient(circle at 20% 25%, rgba(255,255,255,0.25), transparent 40%),
      linear-gradient(160deg, var(--water-light) 0%, var(--water-mid) 50%, var(--water-deep) 100%);
  }
  .card-back .mascot-art { left: 120px; top: 40px; width: 120px; height: 200px; }
  .van-art {
    position: absolute;
    right: 24px; top: 110px;
    width: 210px; height: 110px;
    border-radius: 18px 30px 10px 10px;
    background: linear-gradient(180deg, var(--van-white), #c7d1d9);
  }
  .card-back .brand-name { left: 60px; top: 240px; width: 260px; font-size: 19px; color: var(--card-white); }
</style>
</head>
<body>
  <article class="card card-front">
    <div class="accent-square"></div>
    <h1 class="holder-name">Rodney Ashcombe</h1>
    <div class="contact-band">
      <div class="contact-row">
        <svg viewBox="0 0 24 24" fill="#fff"><path d="M6.6 10.8a15 15 0 006.6 6.6l2.2-2.2a1 1 0 011-.25 11.4 11.4 0 003.6.57 1 1 0 011 1V20a1 1 0 01-1 1A17 17 0 013 4a1 1 0 011-1h3.5a1 1 0 011 1 11.4 11.4 0 00.57 3.6 1 1 0 01-.25 1z"/></svg>
        <span>(555) 218-7730</span>
      </div>
      <div class="contact-row">
        <svg viewBox="0 0 24 24" fill="#fff"><path d="M2 5h20v14H2z M2 5l10 8 10-8" stroke="#0f56ad" stroke-width="1.5"/></svg>
        <span>Info@bramleypipeworks.example</span>
      </div>
      <div class="contact-row">
        <svg viewBox="0 0 24 24" fill="none" stroke="#fff" stroke-width="2"><circle cx="12" cy="12" r="9"/><path d="M3 12h18M12 3c3 3 3 15 0 18M12 3c-3 3-3 15 0 18"/></svg>
        <span>www.bramleypipeworks.example</span>
      </div>
    </div>
    <p class="license">License # <span class="license-number">4627195</span></p>
    <div class="mascot-art" role="img" aria-label="Cartoon plumber mascot holding a pipe wrench and circular saw"></div>
    <p class="brand-name">BRAMLEY PIPEWORKS &amp; More</p>
  </article>

  <article class="card card-back">
    <div class="mascot-art" role="img" aria-label="Cartoon plumber mascot holding a pipe wrench and circular saw"></div>
    <div class="van-art" role="img" aria-label="Cartoon plumber driving a white company van"></div>
    <p class="brand-name">BRAMLEY PIPEWORKS &amp; More</p>
  </article>
</body>
</html>
```